Redesign of business card for Cedar Ridge Mechanical

We are looking for a new design for our business cards for Cedar Ridge Mechanical. We are a plumbing & HVAC construction company, operating on the West Coast of Canada and USA. Logo attached.
Industry/Entity Type
Construction - Plumbing & HVAC
Contact Information for Business Card
Name, address, phone numbers, email, website address
Look and feel
Each slider illustrates characteristics of the customer's brand and the style your logo design should communicate.

```html
<!DOCTYPE html>
<html lang="en">
<head>
<meta charset="utf-8">
<title>Cedar Ridge Mechanical – Business Card</title>
<link href="https://fonts.googleapis.com/css2?family=Oswald:wght@500&family=Montserrat:wght@400;700&display=swap" rel="stylesheet">
<style>
  :root {
    --stage: #2b2b2b;
    --ink: #0a0a0a;
    --paper: #ffffff;
    --stripe: #9a9a9a;
  }
  * { margin: 0; padding: 0; box-sizing: border-box; }
  html, body { width: 1200px; height: 880px; overflow: hidden; background: var(--stage); }
  .canvas { position: relative; width: 1200px; height: 880px; }

  .card {
    position: absolute;
    width: 560px; height: 320px;
    border-radius: 26px;
    overflow: hidden;
    box-shadow: 0 18px 40px rgba(0,0,0,.45);
  }

  /* Front */
  .card--front { left: 60px; top: 80px; background: var(--ink); }
  .brand {
    position: absolute;
    display: flex; align-items: center; gap: 16px;
    font-family: "Oswald", sans-serif;
    font-weight: 500;
    text-transform: uppercase;
    letter-spacing: 2px;
    white-space: nowrap;
  }
  .brand__mark { border: 5px solid currentColor; border-radius: 6px; flex: none; }
  .card--front .brand { left: 50%; top: 50%; transform: translate(-50%, -50%); color: var(--paper); font-size: 34px; }
  .card--front .brand__mark { width: 52px; height: 52px; }

  /* Back */
  .card--back { left: 580px; top: 470px; background: var(--ink); }
  .card__split { position: absolute; inset: 0; }
  .card--back .brand { right: 30px; top: 26px; color: var(--ink); font-size: 22px; gap: 12px; }
  .card--back .brand__mark { width: 32px; height: 32px; border-width: 4px; }

  .contact {
    position: absolute; left: 40px; bottom: 26px;
    color: var(--paper);
    font-family: "Montserrat", sans-serif;
  }
  .contact__name { font-size: 23px; font-weight: 700; letter-spacing: 1px; }
  .contact__role { font-size: 14px; margin-top: 2px; }
  .contact__address { font-size: 14px; line-height: 1.4; margin-top: 14px; }
  .contact__list { list-style: none; margin-top: 12px; font-size: 14px; line-height: 1.6; }
  .contact__list li { display: flex; align-items: center; gap: 10px; }
  .contact__list svg { width: 13px; height: 13px; fill: var(--paper); flex: none; }
</style>
</head>
<body>
<main class="canvas">

  <section class="card card--front" aria-label="Card front">
    <div class="brand"><span class="brand__mark"></span>Cedar Ridge Mechanical</div>
  </section>

  <section class="card card--back" aria-label="Card back">
    <svg class="card__split" viewBox="0 0 560 320" preserveAspectRatio="none" aria-hidden="true">
      <polygon points="80,0 560,0 560,240" fill="var(--paper)"/>
      <polygon points="40,0 80,0 560,240 530,232" fill="var(--stripe)"/>
      <polygon points="0,0 40,0 530,232 560,240 560,320 0,320" fill="var(--ink)"/>
    </svg>

    <div class="brand"><span class="brand__mark"></span>Cedar Ridge Mechanical</div>

    <div class="contact">
      <p class="contact__name">DANIEL MOORE</p>
      <p class="contact__role">Managing Director</p>
      <p class="contact__address">Your address, City<br>State, Zip 1234</p>
      <ul class="contact__list">
        <li><svg viewBox="0 0 24 24"><path d="M6.6 10.8a15 15 0 0 0 6.6 6.6l2.2-2.2a1 1 0 0 1 1-.25 11 11 0 0 0 3.6.57 1 1 0 0 1 1 1V20a1 1 0 0 1-1 1A17 17 0 0 1 3 4a1 1 0 0 1 1-1h3.5a1 1 0 0 1 1 1 11 11 0 0 0 .57 3.6 1 1 0 0 1-.25 1z"/></svg>123 456 789</li>
        <li><svg viewBox="0 0 24 24"><path d="M2 5h20v14H2zm2 2v.5l8 5 8-5V7zm0 3v7h16v-7l-8 5z"/></svg>info@youremail.com</li>
        <li><svg viewBox="0 0 24 24"><path d="M12 2a10 10 0 1 0 0 20 10 10 0 0 0 0-20zm6.9 9h-3a15 15 0 0 0-1.3-6 8 8 0 0 1 4.3 6zM12 4c.9 1.3 1.8 3.7 1.9 7h-3.8C10.2 7.7 11.1 5.3 12 4zM9.4 5a15 15 0 0 0-1.3 6h-3a8 8 0 0 1 4.3-6zM5.1 13h3a15 15 0 0 0 1.3 6 8 8 0 0 1-4.3-6zM12 20c-.9-1.3-1.8-3.7-1.9-7h3.8c-.1 3.3-1 5.7-1.9 7zm2.6-1a15 15 0 0 0 1.3-6h3a8 8 0 0 1-4.3 6z"/></svg>www.yourwebsite.com</li>
      </ul>
    </div>
  </section>

</main>
</body>
</html>
```